I have a logo and need to design the business card and stationery.
Updates

The uploaded logo image named as GREYMARSH CONSTRUCTION which is to be replaced to GREYMARSH CONTRACTS. Kindly add below details and submit the designs- Company name- Greymarsh Engineering Contracts LLP Name & Post- Kelvan Joshi (Designated Partner) Address- Block No.317, Wing C, Tulvo Trade Court, Manek Pural Road, Ruparel Industrial Estate, Goregaon(E), Mumbai - 400 063 Contact- +91 97415 60382 Email- kelvanjoshi@mailbrook.example Website- www.greymarshcontracts.example Contact for Letterhead- +91-22-28754193

Hi Tovin Rahul, We are liking your Design #28860835. We have suggested some changes which are mentioned in feedback. Kindly revert with it asap to finalize this design.

Colors

Designer to choose colors to be used in the design.

```html
<!DOCTYPE html>
<html lang="en">
<head>
<meta charset="utf-8">
<title>Greymarsh Contracts — Business Card</title>
<link rel="stylesheet" href="https://fonts.googleapis.com/css2?family=Roboto+Condensed:wght@400;700&display=swap">
<style>
  :root {
    --stage: #3a3a3a;
    --card: #141414;
    --card-edge: #2a2a2a;
    --pattern: #1f1f1f;
    --ink: #ffffff;
    --ink-soft: #d4d4d4;
    --rule: #bdbdbd;
  }
  * { margin: 0; padding: 0; box-sizing: border-box; }
  html, body { width: 1200px; height: 1129px; overflow: hidden; }
  body {
    background: var(--stage);
    font-family: "Roboto Condensed", Arial, sans-serif;
    color: var(--ink);
    position: relative;
  }
  .card {
    position: absolute;
    background: var(--card);
    border: 1px solid var(--card-edge);
    overflow: hidden;
  }
  .card--back { left: 70px; top: 90px; width: 620px; height: 354px; }
  .card--front { left: 750px; top: 330px; width: 380px; height: 665px; }

  .back-pattern {
    position: absolute;
    inset: 0;
    background: linear-gradient(135deg, var(--pattern), var(--card) 55%, var(--pattern));
  }
  .back-mark {
    position: absolute;
    left: 470px;
    top: 200px;
    width: 48px;
    height: 48px;
    background: var(--ink);
  }

  .front-content {
    position: absolute;
    inset: 56px 30px 40px;
    display: flex;
    flex-direction: column;
    align-items: center;
    text-align: center;
  }
  .brand { display: flex; flex-direction: column; align-items: center; gap: 14px; margin-bottom: 34px; }
  .brand__square { width: 92px; height: 92px; background: var(--ink); }
  .brand__name { font-weight: 700; font-size: 40px; line-height: 1; letter-spacing: 0.5px; }
  .brand__name span { display: block; font-size: 19px; letter-spacing: 15px; margin-top: 6px; padding-left: 15px; }

  .person__name { font-weight: 700; font-size: 25px; letter-spacing: 0.5px; line-height: 1.15; }
  .person__role { font-size: 19px; line-height: 1.3; margin-bottom: 14px; }

  .icon-row { display: flex; align-items: center; gap: 7px; margin-bottom: 12px; }
  .icon-row__rule { width: 40px; height: 1px; background: var(--rule); margin: 0 10px; }
  .icon { width: 24px; height: 24px; display: block; }

  .contacts { font-size: 18px; line-height: 25px; }
  .divider { width: 200px; height: 1px; background: var(--rule); margin: 14px 0 12px; }
  .address { font-style: normal; font-size: 15px; line-height: 20px; color: var(--ink-soft); }
  .address__company { color: var(--ink); }
</style>
</head>
<body>

<section class="card card--back">
  <div class="back-pattern" role="img" aria-label="Tonal repeat pattern in dark spot gloss"></div>
  <div class="back-mark"></div>
</section>

<section class="card card--front">
  <div class="front-content">
    <div class="brand">
      <div class="brand__square"></div>
      <div class="brand__name">GREYMARSH<span>CONTRACTS</span></div>
    </div>

    <div class="person__name">KELVAN JOSHI</div>
    <div class="person__role">Designated Partner</div>

    <div class="icon-row">
      <span class="icon-row__rule"></span>
      <svg class="icon" viewBox="0 0 20 20" aria-label="Mobile">
        <rect width="20" height="20" rx="4" fill="#fff"/>
        <path d="M6 4l2.5 0 1 3-1.5 1.2a7 7 0 0 0 3.8 3.8L13 10.5l3 1V14a2 2 0 0 1-2 2A10 10 0 0 1 4 6a2 2 0 0 1 2-2z" fill="#141414"/>
      </svg>
      <svg class="icon" viewBox="0 0 20 20" aria-label="Office phone">
        <rect width="20" height="20" rx="4" fill="#fff"/>
        <rect x="4" y="5" width="12" height="3" rx="1" fill="#141414"/>
        <rect x="5" y="9" width="10" height="7" rx="1" fill="#141414"/>
        <circle cx="10" cy="12.5" r="1.8" fill="#fff"/>
      </svg>
      <svg class="icon" viewBox="0 0 20 20" aria-label="Email">
        <rect width="20" height="20" rx="4" fill="#fff"/>
        <rect x="4" y="6" width="12" height="8" fill="none" stroke="#141414" stroke-width="1.4"/>
        <path d="M4 6l6 5 6-5" fill="none" stroke="#141414" stroke-width="1.4"/>
      </svg>
      <svg class="icon" viewBox="0 0 20 20" aria-label="Website">
        <rect width="20" height="20" rx="4" fill="#fff"/>
        <circle cx="10" cy="10" r="6" fill="none" stroke="#141414" stroke-width="1.4"/>
        <ellipse cx="10" cy="10" rx="2.6" ry="6" fill="none" stroke="#141414" stroke-width="1.2"/>
        <path d="M4 10h12" stroke="#141414" stroke-width="1.2"/>
      </svg>
      <span class="icon-row__rule"></span>
    </div>

    <div class="contacts">
      <div>+91 97415 60382</div>
      <div>+91-22-28754193</div>
      <div>kelvanjoshi@mailbrook.example</div>
      <div>www.greymarshcontracts.example</div>
    </div>

    <div class="divider"></div>

    <address class="address">
      <div class="address__company">Greymarsh Engineering Contracts LLP</div>
      <div>Block No.317, Wing C, Tulvo Trade Court,</div>
      <div>Manek Pural Road, Ruparel Industrial Estate,</div>
      <div>Goregaon(E), Mumbai - 400 063</div>
    </address>
  </div>
</section>

</body>
</html>
```